Ward Compass Business Card Design*

We need a business card design for our company Ward Compass. Our company is specialized in providing online consulting services regarding medical institutions, hospitals and doctors. We work with patients worldwide looking to choose between healthcare providers. We have a website you may use as a reference, where we list doctors and clinics worldwide. So we target Medical providers as well as patients worldwide.
Target Market(s)
Medical Providers and patients around the world
Industry/Entity Type
Medical
Contact Information for Business Card
Salwa Kettani
CEO
+90 612 348 2175
info@wardcompass.example
www.wardcompass.example
14 Annakhil 7 H.R.B. Rabat, Morocco
Requirements
Must have
- Company logo/name on one full side, personal info and smaller logo and company name on the other side.
Nice to have
- Smart and elegant design

```html
<!DOCTYPE html>
<html lang="en">
<head>
<meta charset="utf-8">
<title>Ward Compass Business Card</title>
<link rel="stylesheet" href="https://fonts.googleapis.com/css2?family=Lato:wght@400;700&display=swap">
<style>
  :root {
    --backdrop: #d9dadc;
    --card-white: #ffffff;
    --brand-blue: #2a74bd;
    --brand-light: #2f9bd6;
    --ink: #2b2b2b;
    --rule: #b9b9b9;
    --grad-top: #32a5da;
    --grad-bottom: #2f70b5;
  }
  * { margin: 0; padding: 0; box-sizing: border-box; }
  html, body {
    width: 1200px;
    height: 802px;
    overflow: hidden;
    background: var(--backdrop);
    font-family: "Lato", Arial, sans-serif;
  }
  .canvas { position: relative; width: 1200px; height: 802px; }
  .card {
    position: absolute;
    top: 274px;
    width: 442px;
    height: 265px;
    box-shadow: 0 3px 8px rgba(0,0,0,0.25);
  }
  .card--front { left: 136px; background: var(--card-white); }
  .card--back {
    left: 624px;
    background: linear-gradient(180deg, var(--grad-top), var(--grad-bottom));
  }
  .brand {
    position: absolute;
    display: flex;
    align-items: center;
    white-space: nowrap;
  }
  .brand__dot { border-radius: 50%; flex: none; }
  .brand__name { font-weight: 400; letter-spacing: 0.5px; }
  .card--front .brand { left: 172px; top: 54px; gap: 12px; }
  .card--front .brand__dot { width: 44px; height: 44px; background: var(--brand-blue); }
  .card--front .brand__name { font-size: 22px; color: var(--brand-blue); }
  .card--back .brand { left: 100px; top: 104px; gap: 14px; }
  .card--back .brand__dot { width: 52px; height: 52px; background: var(--card-white); }
  .card--back .brand__name { font-size: 26px; color: var(--card-white); }
  .holder { position: absolute; left: 25px; top: 152px; }
  .holder__name { font-size: 16px; color: var(--brand-blue); letter-spacing: 0.2px; }
  .holder__name strong { font-weight: 700; }
  .holder__role { font-size: 12.5px; color: var(--ink); margin-top: 1px; }
  .rule {
    position: absolute;
    left: 56px; top: 183px;
    width: 358px; height: 1px;
    background: var(--rule);
  }
  .contact {
    position: absolute;
    left: 25px; top: 209px;
    font-size: 12.5px;
    color: var(--ink);
    line-height: 16px;
  }
  .contact__row { display: flex; align-items: center; gap: 3px; }
  .contact__row svg { width: 11px; height: 11px; fill: var(--brand-blue); }
  .website {
    position: absolute;
    right: 28px; top: 225px;
    font-size: 12.5px;
    color: var(--brand-blue);
    line-height: 16px;
  }
</style>
</head>
<body>
<main class="canvas">
  <section class="card card--front" aria-label="Business card, contact side">
    <div class="brand">
      <span class="brand__dot"></span>
      <span class="brand__name">WARD COMPASS</span>
    </div>
    <div class="holder">
      <p class="holder__name"><strong>SALWA</strong> KETTANI</p>
      <p class="holder__role">CEO</p>
    </div>
    <div class="rule"></div>
    <div class="contact">
      <p class="contact__row">
        <svg viewBox="0 0 12 12" aria-hidden="true"><path d="M1 4c0-2 2-3 5-3s5 1 5 3l-2 1-1-2H4L3 5zM3 6h6l1 5H2z"/></svg>
        +90 612 348 2175
      </p>
      <p class="contact__row">
        <svg viewBox="0 0 12 12" aria-hidden="true"><path d="M1 3h10v7H1zM1.8 3.6v.6L6 7l4.2-2.8v-.6L6 6.3z" fill-rule="evenodd"/></svg>
        info@wardcompass.example
      </p>
    </div>
    <p class="website">www.wardcompass.example</p>
  </section>

  <section class="card card--back" aria-label="Business card, brand side">
    <div class="brand">
      <span class="brand__dot"></span>
      <span class="brand__name">WARD COMPASS</span>
    </div>
  </section>
</main>
</body>
</html>
```